Website redesign for job agency recruitment

Please refer to the attached document, “Tarvenly Work Website Brief,” for comprehensive details regarding the scope, objectives, and requirements of this website redesign project.

For imagery you can use images from this website https://www.pixelmarrowfoto.com or any other you regularly use.

Target Market(s)

Jobseekers and Companies looking for general labour

Industry/Entity Type

Services: Oil, Gas and Mining, Administrative, Construction and Trades, Warehouse and Logistics and, Manufacturing.

Number of Pages Required

5+ page

Font styles to use
Serif
Other font styles liked:
• Inter, Open-Sans or similar.

Requirements
Must have
• The requirements highlighted in the Word document attached. The final design needs to be provided in Figma including all viewports (Desktop, mobiel and tablet)
Should not have
• Website we like as a reference: www.brevicktalentco.com, www.qelvaworks.com, www.zunmarra.com, www.ferrowhires.com, www.9vtalentpool.com, www.hiringwithtrello.ca

```html
<!DOCTYPE html>
<html lang="en">
<head>
<meta charset="utf-8">
<title>Tarvenly Work Agency Ltd. – Home</title>
<link href="https://fonts.googleapis.com/css2?family=Montserrat:wght@400;500;600;700;800&display=swap" rel="stylesheet">
<style>
:root{
  --navy:#1b2f7d;
  --navy-deep:#10306f;
  --yellow:#f2c018;
  --yellow-soft:#f5d34a;
  --sky:#3d9fdb;
  --white:#ffffff;
  --ink:#1d2a55;
}
*{margin:0;padding:0;box-sizing:border-box}
html,body{width:1200px;height:2758px;overflow:hidden}
body{position:relative;background:var(--white);font-family:"Montserrat",sans-serif;color:var(--ink)}
.abs{position:absolute}
a{color:inherit;text-decoration:none}

/* Hero */
.hero-photo{left:0;top:0;width:1200px;height:700px;
  background:linear-gradient(90deg,#4aa6df 0,#3e9bd8 38%,#f6bd2a 40.8%,#ffc83a 48%,#f6bd2a 55.4%,#3c9ad6 57.5%,#55b1e6 100%)}
.hero-curve{left:0;top:0;width:1200px;height:700px}
.brand{display:flex;align-items:center;gap:10px}
.brand .dot{width:34px;height:34px;border-radius:50%;background:var(--yellow)}
.brand-name{font-weight:700;font-size:20px;color:var(--navy);line-height:1.1}
.brand-sub{font-size:9px;color:#6a7596;margin-top:4px}
.hero-brand{left:102px;top:60px}
.toll{left:875px;top:0;width:325px;height:55px;background:var(--yellow);border-bottom-left-radius:30px;
  display:flex;align-items:center;padding-left:32px;font-size:13px;color:var(--navy);gap:8px}
.nav{left:647px;top:78px;display:flex;gap:0;align-items:center;font-size:13px;color:var(--navy)}
.nav a{padding:6px 15px}
.nav .active{background:var(--navy);color:var(--white);border-radius:14px;font-weight:700}
.hero-title{left:0;width:1200px;top:240px;text-align:center;font-size:68px;font-weight:700;color:var(--navy);letter-spacing:-0.5px}
.btn{height:46px;border-radius:23px;display:flex;align-items:center;justify-content:center;font-weight:700;font-size:17px}
.btn-navy{left:388px;top:353px;width:205px;background:var(--navy);color:var(--yellow)}
.btn-yellow{left:608px;top:351px;width:205px;background:var(--yellow);color:var(--white)}
.slider-dots{left:102px;top:270px;display:flex;flex-direction:column;gap:12px}
.slider-dots span{width:10px;height:10px;border-radius:50%;background:var(--yellow);border:1.5px solid #fff}
.slider-dots .on{background:var(--navy)}

/* Services */
.services-mark{left:103px;top:870px;font-size:50px;font-weight:800;color:var(--navy);line-height:1}
.service-link{font-size:14px;color:var(--navy);font-weight:500}
.service-hl{left:338px;top:767px;width:203px;height:33px;border:1.5px dashed var(--yellow);border-radius:50%;
  display:flex;align-items:center;justify-content:center;color:var(--yellow);font-weight:700;font-size:14px}
.dotgrid{background-image:radial-gradient(circle,var(--yellow) 1.7px,transparent 2.2px);background-size:39px 39px}
.service-card{left:660px;top:790px;width:254px;height:302px;border-top-left-radius:110px;
  background:linear-gradient(135deg,#f7d85a,#f2c018 60%);padding:46px 26px 0 30px;text-align:right}
.service-card h3{font-size:17px;font-weight:700;color:var(--navy);margin-bottom:12px}
.service-card p{font-size:12.6px;line-height:21px;color:var(--ink)}
.card-bar{left:908px;top:835px;width:4px;height:26px;background:var(--navy)}
.photo-rig{left:929px;top:727px;width:169px;height:181px;border-top-right-radius:120px;background:linear-gradient(160deg,#d9dadc,#8b8e93)}
.photo-worker{left:865px;top:938px;width:233px;height:250px;background:linear-gradient(135deg,#c79a1e,#3b3d45 70%)}

/* About */
.about-shape{left:0;top:1200px;width:1200px;height:710px}
.about-title{left:110px;top:1393px;font-size:44px;font-weight:700;color:var(--white)}
.about-rule{left:108px;top:1452px;width:72px;height:4px;background:var(--yellow)}
.about-text{left:110px;top:1477px;width:480px;font-size:13.4px;line-height:21.2px;color:var(--white)}
.about-text p+p{margin-top:21px}
.btn-outline{left:104px;top:1737px;width:156px;height:47px;border:1.5px solid var(--yellow);border-radius:24px;
  color:var(--white);font-weight:700;font-size:17px;display:flex;align-items:center;justify-content:center}
.photo-office{left:610px;top:1372px;width:590px;height:431px;border-top-left-radius:170px;
  background:linear-gradient(120deg,#6b6a66,#a9a59c 45%,#d6d4cf)}

/* Banner */
.banner{left:0;top:1905px;width:1200px;height:543px;background:linear-gradient(180deg,#d8b024,#c9a219 55%,#b8921a)}
.banner-text{left:0;top:2117px;width:1200px;text-align:center;font-size:44px;font-weight:700;color:var(--white);line-height:49px}

/* Footer */
.footer-brand{left:100px;top:2575px}
.foot-title{font-size:19px;font-weight:700;color:var(--navy)}
.foot-list{list-style:none;font-size:13.4px;color:var(--navy);line-height:21.3px}
.foot-list li::before{content:"›";display:inline-block;width:22px;font-size:16px}
.social{list-style:none;font-size:13.4px;color:var(--navy)}
.social li{display:flex;align-items:center;gap:10px;height:32px}
.social .ring{width:26px;height:26px;border-radius:50%;border:1.5px solid var(--navy)}
.copyright{left:0;width:1200px;top:2696px;text-align:center;font-size:13px;color:var(--navy)}
</style>
</head>
<body>

<!-- Hero -->
<div class="abs hero-photo" role="img" aria-label="Row of blue chairs with one yellow chair against a blue and yellow wall"></div>
<svg class="abs hero-curve" viewBox="0 0 1200 700" aria-hidden="true">
  <path d="M0,548 Q330,690 700,672 Q1000,650 1200,546 L1200,700 L0,700Z" fill="#fff"/>
  <path d="M0,556 Q320,690 700,674 Q340,712 0,618Z" fill="#f2c018"/>
</svg>
<div class="abs toll"><svg width="14" height="14" viewBox="0 0 24 24"><path fill="#1b2f7d" d="M6.6 10.8a15.1 15.1 0 0 0 6.6 6.6l2.2-2.2c.3-.3.7-.4 1-.2 1.1.4 2.3.6 3.6.6.6 0 1 .4 1 1V20c0 .6-.4 1-1 1C10.6 21 3 13.4 3 4c0-.6.4-1 1-1h3.5c.6 0 1 .4 1 1 0 1.3.2 2.5.6 3.6.1.3 0 .7-.2 1z"/></svg>Toll Free : 1-800-555-0147</div>
<div class="abs brand hero-brand"><span class="dot"></span><div><div class="brand-name">Tarvenly Work<br>Agency Ltd.</div><div class="brand-sub">The right people to power your business</div></div></div>
<nav class="abs nav"><a class="active">Home</a><a>Candidates</a><a>Employers</a><a>About Us</a><a>Contact Us</a></nav>
<div class="abs slider-dots"><span></span><span class="on"></span><span></span><span></span><span></span></div>
<h1 class="abs hero-title">Our goal is your success</h1>
<a class="abs btn btn-navy">For Candidates</a>
<a class="abs btn btn-yellow">For Employers</a>

<!-- Services -->
<div class="abs service-hl">Oil, Gas and Mining</div>
<svg class="abs" style="left:320px;top:798px" width="60" height="40" aria-hidden="true"><path d="M52,2 Q40,28 4,38" fill="none" stroke="#f2c018" stroke-width="1.5" stroke-dasharray="4 3"/></svg>
<div class="abs services-mark">TWA<br>Services</div>
<div class="abs service-link" style="left:417px;top:842px">Administrative</div>
<div class="abs service-link" style="left:448px;top:909px">Construction and Trades</div>
<div class="abs service-link" style="left:416px;top:977px">Warehouse and Logistics</div>
<div class="abs service-link" style="left:368px;top:1047px">Manufacturing</div>
<div class="abs dotgrid" style="left:596px;top:975px;width:160px;height:150px"></div>
<div class="abs dotgrid" style="left:976px;top:694px;width:150px;height:150px"></div>
<div class="abs photo-rig" role="img" aria-label="Offshore oil rig in black and white"></div>
<div class="abs photo-worker" role="img" aria-label="Worker in hard hat checking yellow pipework"></div>
<div class="abs service-card">
  <h3>Oil, Gas and Mining</h3>
  <p>Tarvenly Work Agency is a premiere Oil, Gas &amp; Mining staffing agency that can provide you with a reliable and experienced workforce. From rig hands to engineers, we provide solutions from temp, temp-to-hire, and permanent positions.</p>
</div>
<div class="abs card-bar"></div>

<!-- About -->
<svg class="abs about-shape" viewBox="0 0 1200 710" aria-hidden="true">
  <path d="M0,170 Q330,40 690,40 Q1000,44 1200,170 L1200,710 L0,710Z" fill="#10306f"/>
  <path d="M0,102 Q300,12 700,38 Q300,30 0,158Z" fill="#f2c018"/>
</svg>
<div class="abs dotgrid" style="left:596px;top:1366px;width:190px;height:160px"></div>
<div class="abs dotgrid" style="left:1026px;top:1800px;width:180px;height:80px"></div>
<h2 class="abs about-title">About Us</h2>
<div class="abs about-rule"></div>
<div class="abs about-text">
  <p>Tarvenly Work Agency offers a complete range of staffing services to keep pace with your career or operational demands. We understand it's not only daunting but very costly in both time and money to make your business thrive in a rapidly changing environment.</p>
  <p>Our staffing and recruitment services are not just limited to finding good people. We are a Canada-wide team of capable search specialists, career counselors, HR specialists, and business consultants who enjoy providing our clients with a very customized staffing solution that evolves within their market. Each project provides a chance for us to apply our knowledge and shine.</p>
</div>
<a class="abs btn-outline">Read More</a>
<div class="abs photo-office" role="img" aria-label="Team meeting in a glass-walled office"></div>

<!-- Banner -->
<div class="abs banner" role="img" aria-label="Smiling colleagues applauding in a yellow-toned meeting"></div>
<div class="abs banner-text">Tarvenly Work Agency.<br>The right people to power your business!</div>

<!-- Footer -->
<div class="abs brand footer-brand"><span class="dot"></span><div><div class="brand-name">Tarvenly Work<br>Agency Ltd.</div><div class="brand-sub">The right people to power your business</div></div></div>
<div class="abs foot-title" style="left:370px;top:2521px">Quick Links</div>
<ul class="abs foot-list" style="left:370px;top:2555px"><li>Home</li><li>Candidates</li><li>Employers</li><li>About Us</li><li>Contact Us</li></ul>
<ul class="abs foot-list" style="left:518px;top:2555px"><li>Oil, Gas &amp; Mining</li><li>Administrative</li><li>Construction &amp; Trades</li><li>Warehouse &amp; Logistics</li><li>Manufacturing</li></ul>
<ul class="abs foot-list" style="left:739px;top:2555px"><li>Vancouver Location</li><li>Client Registration</li><li>Terms of Use</li></ul>
<div class="abs foot-title" style="left:960px;top:2521px">Follow Us</div>
<ul class="abs social" style="left:961px;top:2554px">
  <li><span class="ring"></span>Socialane</li>
  <li><span class="ring"></span>Chirpwave</li>
  <li><span class="ring"></span>Workgrid</li>
  <li><span class="ring"></span>Clipstream</li>
</ul>
<div class="abs copyright">© 2026 | www.tarvenlyworkagency.com</div>

</body>
</html>
```